Marigold Synchronized Swim Team's Clubhouse (web page)

Fun, Super Easy to read and navigate. Please error on the side of too large font sizes rather than too small font sizes.

We are a New Orleans (USA) based club for adults and youth of all genders.

We have youth and adult performance and competition teams. We teach synchronized swimming. We perform at special events.

Webpage should allow for

1. Sign up for classes, camps and teams (pay fees, sign waivers, reserve a spot and link to national Delmar Aquaform club membership website in order to buy required national membership).Make our multi step registration process easy, quick, pleasant.

2. Provide an area to upload practice schedules.
and performance calendar.

3. Easily
Hire one of our synchro squad to perform at special events.

4. Embedded Google Calndar

5 Members only site
( one away for youth and one area for adults. )

6 Show off our new logo, photos and videos. Be able to change these images often.

Our team colors are red, aqua and pink.

7. Buy logo gear

Click to team shop at
Brindle cove.com and other future team shops.

8. One click to become a sponsor of the team.

An area to show off sponsor logos. We will have several levels of sponsorships. It is important to have small medium and large logo spots. WE also will have a wall of names of folks who donate 10 - 100 dollars to sponsor the team.

We want the experience to be fun . We do not want headache producing events.

Our team colors are red, pink and aqua. WE have not settled on a specific red or pink yet. You are free to play around with different tones and hues. I tend toward a sholcking pink and cherry red. But really do want to see what your thoughts are for our reds and pinks. Also feel free to vary aqua from a light to dark. But we do want to stay away from navy.
Thanks for your hard work and creativity.

Target Market(s)

All ages, genders and ethnicity. Swimmers, dancers and event planners.

Coding

Coded - Design and coding required

Number of Pages Required

4 page

Font styles to use
Sans Serif

Colors
ec1f27
0293ce
f59195

Requirements
Must have
• See p descriptions +
• Fine #20 is our logo and
• Playful, bold, elegant, Colorful (red, aqua and pink are our team colors).
• I want to be able to plug in / update photos , schedules, release forms, almost everything as our seasons change. I do not know ( Newbury) do I want coded or incised site. All advice welcome.
Nice to have
• Your flare as a designer. Thank you for making us better through your creativity, ability to edit, clarify and advice. :-)
Should not have
• Confusion.

```html
<!DOCTYPE html>
<html lang="en">
<head>
<meta charset="utf-8">
<title>Marigold Synchronized Swim Team – Clubhouse</title>
<link href="https://fonts.googleapis.com/css2?family=Exo+2:wght@500;600;700&family=Michroma&family=Open+Sans:wght@400;600;700&display=swap" rel="stylesheet">
<style>
:root{
  --red:#ec1f27;
  --aqua:#0293ce;
  --pink:#f59195;
  --ink:#1c1c1c;
  --text:#444;
  --muted:#8a8a8a;
  --line:#e3e3e3;
  --band:#eef1f3;
  --footer:#1789c8;
  --footer-dark:#0f78b3;
  --cal-cell:#d9d9d9;
}
*{box-sizing:border-box;margin:0;padding:0}
html,body{width:1200px;height:3516px;overflow:hidden}
body{position:relative;background:#fff;font-family:"Open Sans",Arial,sans-serif;color:var(--text)}
.abs{position:absolute}
.heading{font-family:"Exo 2",Arial,sans-serif;font-weight:700;color:var(--ink);letter-spacing:2px;text-transform:uppercase}

/* header */
.header{left:0;top:0;width:1200px;height:100px;background:#fff;border-top:4px solid var(--aqua);z-index:5}
.brand{left:72px;top:8px;width:172px;height:172px;border-radius:50%;background:#fff;box-shadow:0 2px 8px rgba(0,0,0,.15);display:flex;flex-direction:column;align-items:center;justify-content:center;z-index:6}
.brand-dot{width:56px;height:56px;border-radius:50%;background:var(--aqua);margin-bottom:8px}
.brand-name{font-family:"Exo 2",Arial,sans-serif;font-weight:700;font-size:22px;color:var(--aqua);letter-spacing:1px}
.topline{right:74px;top:18px;display:flex;align-items:center;gap:24px;font-size:16px;color:#333}
.topline span{display:flex;align-items:center;gap:8px}
.signup{border:2px solid var(--red);border-radius:4px;padding:4px 12px;color:var(--red);font-weight:700;font-size:14px}
.nav{right:74px;top:64px;display:flex;gap:32px;font-family:"Exo 2",Arial,sans-serif;font-weight:600;font-size:15px;color:#222;text-transform:uppercase}
.nav .active{color:var(--red);border-bottom:3px solid var(--red);padding-bottom:4px}

/* hero */
.hero{left:0;top:100px;width:1200px;height:462px;background:linear-gradient(180deg,#4b8a90 0%,#2f7f8a 40%,#3b9aa6 75%,#5fb3bd 100%)}
.hero-title{left:0;top:120px;width:1200px;text-align:center;font-family:"Michroma",Arial,sans-serif;font-size:78px;color:#fff;letter-spacing:2px}
.hero-sub{left:0;top:215px;width:1200px;text-align:center;font-size:28px;font-weight:600;color:#fff}
.hero-btns{left:0;top:276px;width:1200px;display:flex;justify-content:center;gap:22px}
.btn{width:210px;height:40px;display:flex;align-items:center;justify-content:center;font-family:"Exo 2",Arial,sans-serif;font-weight:700;font-size:15px;color:#fff;text-transform:uppercase;letter-spacing:1px;border-radius:3px}
.btn-red{background:var(--red)}
.btn-ghost{border:2px solid #fff;background:rgba(0,0,0,.2)}
.arrow-btn{top:205px;width:34px;height:34px;border-radius:50%;background:rgba(0,0,0,.35);display:flex;align-items:center;justify-content:center}
.hero-wave{left:0;top:440px;width:1200px;height:124px}

/* upload band */
.band{left:0;top:562px;width:1200px;height:134px;background:var(--band)}
.band-text{left:98px;top:30px;width:700px;font-size:22px;font-weight:600;color:#222;line-height:1.45}
.upload{right:98px;top:44px;border:2px solid var(--red);border-radius:4px;padding:10px 18px;font-family:"Exo 2",Arial,sans-serif;font-weight:700;font-size:14px;color:var(--red);text-transform:uppercase;display:flex;gap:10px;align-items:center;background:#fff}

/* registration */
.reg-title{left:0;top:744px;width:1200px;text-align:center;font-size:30px}
.reg-intro{left:170px;top:800px;width:860px;text-align:center;font-size:12px;line-height:1.8;color:var(--muted)}
.step{top:878px;width:260px;text-align:center}
.step-circle{width:164px;height:164px;border-radius:50%;border:2px solid var(--line);margin:0 auto;display:flex;align-items:center;justify-content:center;background:#fff}
.step-label{margin-top:30px;font-size:20px;font-weight:600;color:#222}
.step-text{margin:10px auto 0;width:220px;font-size:12px;line-height:1.7;color:var(--muted)}
.step-arrow{top:930px}
.rule{left:98px;width:1004px;height:1px;background:var(--line)}

/* events */
.col-title{font-size:30px}
.event{left:98px;width:605px;height:212px;border-bottom:1px solid var(--line)}
.event-img{position:absolute;left:0;top:0;width:234px;height:188px;border:4px solid #fff;box-shadow:0 0 0 1px #ddd}
.event-body{position:absolute;left:262px;top:4px;width:343px}
.event-title{font-size:15.5px;font-weight:600;color:#222;white-space:nowrap}
.meta{margin-top:10px;font-size:11px;color:var(--muted);display:flex;gap:12px;white-space:nowrap}
.meta b{color:var(--aqua);font-weight:400}
.event-text{margin-top:10px;font-size:11.5px;line-height:1.7;color:var(--muted)}
.more{font-family:"Exo 2",Arial,sans-serif;font-weight:700;font-size:13px;color:var(--red);text-transform:uppercase}

/* calendar */
.calendar{left:764px;top:1313px;width:338px;height:324px;border:1px solid var(--line);padding:10px}
.cal-head{height:44px;background:var(--aqua);color:#fff;display:flex;align-items:center;justify-content:space-between;padding:0 14px;font-family:"Exo 2",Arial,sans-serif;font-weight:700;font-size:18px}
.cal-grid{display:grid;grid-template-columns:repeat(7,1fr);gap:4px;margin-top:10px;text-align:center}
.cal-grid .dow{font-weight:700;font-size:16px;color:#222;height:30px;line-height:30px}
.cal-grid .d{background:var(--cal-cell);height:34px;line-height:34px;font-size:16px;color:#222}
.cal-grid .d.empty{background:none}
.cal-grid .d.today{background:var(--red);color:#fff}

/* news */
.news-item{left:764px;width:338px;height:94px;border-bottom:1px solid var(--line)}
.news-img{position:absolute;left:0;top:10px;width:106px;height:70px}
.news-body{position:absolute;left:130px;top:14px;width:208px}
.news-title{font-size:14px;font-weight:600;color:#222;white-space:nowrap}
.video{left:764px;top:2257px;width:338px;height:188px;border:4px solid #fff;box-shadow:0 0 0 1px #ddd;background:linear-gradient(135deg,#2aa7b5,#6fc8cf 55%,#2b8f9c)}
.play{left:908px;top:2326px;width:50px;height:50px;border-radius:50%;background:rgba(0,0,0,.75);display:flex;align-items:center;justify-content:center}

/* photos */
.photos{left:98px;top:2606px;width:605px;height:268px;display:grid;grid-template-columns:repeat(4,1fr);grid-template-rows:repeat(2,1fr);gap:4px}
.photos div{width:100%;height:100%}
.feed{left:741px;top:2606px;width:361px;height:268px;border:1px solid var(--line);background:#f6f7f9}
.feed-cover{position:absolute;left:0;top:0;width:359px;height:160px;background:linear-gradient(160deg,#3c9db0,#7cc3cf 60%,#4aa3b5)}
.feed-badge{position:absolute;left:14px;top:14px;width:86px;height:86px;background:#fff;border:2px solid #fff;display:flex;align-items:center;justify-content:center}
.feed-name{position:absolute;left:112px;top:18px;color:#fff;font-weight:700;font-size:16px}
.feed-likes{position:absolute;left:112px;top:40px;color:#fff;font-size:12px}
.feed-btn{position:absolute;top:108px;background:#f4f4f4;border:1px solid #ccc;font-size:12px;font-weight:700;color:#333;padding:5px 12px;border-radius:2px}
.feed-note{position:absolute;left:14px;top:172px;font-size:12px;color:#666}
.feed-faces{position:absolute;left:14px;top:196px;display:flex;gap:6px}
.feed-faces div{width:40px;height:40px}

/* sponsors */
.sponsors{left:0;top:2930px;width:1200px;height:260px;background:var(--band)}
.sp-title{left:0;top:2972px;width:1200px;text-align:center;font-size:30px}
.sp-row{left:132px;top:3033px;width:936px;display:flex;justify-content:space-between}
.sp-logo{width:172px;height:82px;background:#fff;border:1px solid #ddd;display:flex;align-items:center;justify-content:center;font-family:"Open Sans",Arial,sans-serif;font-weight:600;font-size:24px;color:#777}
.sp-arrow{top:3062px}
.foot-wave{left:0;top:3110px;width:1200px;height:90px}

/* footer */
.footer{left:0;top:3190px;width:1200px;height:326px;background:var(--footer)}
.f-col{top:3224px;color:#fff}
.f-head{font-family:"Exo 2",Arial,sans-serif;font-weight:600;font-size:19px;margin-bottom:14px}
.f-list{list-style:none;font-size:12.5px;line-height:2.05}
.f-contact{font-size:12.5px;line-height:1.6;display:flex;gap:14px;margin-bottom:18px}
.f-input{display:flex;margin-top:16px}
.f-input .field{width:230px;height:38px;background:#fff;color:#999;font-size:12px;padding:11px 12px}
.f-input .go{width:92px;height:38px;background:var(--red);color:#fff;font-weight:700;font-size:12px;display:flex;align-items:center;justify-content:center;text-transform:uppercase}
.socials{display:flex;gap:8px;margin-top:12px}
.socials span{width:32px;height:32px;border-radius:50%;border:2px solid #fff}
.copy{left:0;top:3470px;width:1200px;text-align:center;font-size:12px;color:#fff;border-top:1px solid rgba(255,255,255,.25);padding-top:12px}
</style>
</head>
<body>

<!-- header -->
<div class="abs header">
  <div class="abs topline">
    <span><svg width="16" height="16" viewBox="0 0 24 24"><path fill="#ec1f27" d="M6.6 10.8a15 15 0 006.6 6.6l2.2-2.2c.3-.3.7-.4 1-.2 1.1.4 2.3.6 3.6.6.6 0 1 .4 1 1V20c0 .6-.4 1-1 1A17 17 0 013 4c0-.6.4-1 1-1h3.5c.6 0 1 .4 1 1 0 1.3.2 2.5.6 3.6.1.3 0 .7-.2 1z"/></svg>1 555 010 0199</span>
    <span><svg width="18" height="14" viewBox="0 0 24 18"><rect x="1" y="1" width="22" height="16" rx="2" fill="none" stroke="#ec1f27" stroke-width="2"/><path d="M1 2l11 8 11-8" fill="none" stroke="#ec1f27" stroke-width="2"/></svg>hello@marigoldclub.org</span>
    <span class="signup">✎ SIGN UP</span>
  </div>
  <nav class="abs nav">
    <span class="active">Home</span><span>About Us</span><span>Services</span><span>Special Events</span><span>Shop</span><span>Sponsor</span><span>Contact Us</span>
    <svg width="16" height="16" viewBox="0 0 24 24"><circle cx="10" cy="10" r="7" fill="none" stroke="#222" stroke-width="3"/><path d="M15 15l7 7" stroke="#222" stroke-width="3"/></svg>
  </nav>
</div>
<div class="abs brand"><div class="brand-dot"></div><div class="brand-name">MARIGOLD</div></div>

<!-- hero -->
<section class="abs hero" role="img" aria-label="Photo of a synchronized swimmer in a pool">
  <div class="abs hero-title">MARIGOLD</div>
  <div class="abs hero-sub">Nola's Marigold Synchronized Swim Team</div>
  <div class="abs hero-btns"><span class="btn btn-red">Become a Sponsor</span><span class="btn btn-ghost">Team Shop</span></div>
  <div class="abs arrow-btn" style="left:34px"><svg width="12" height="14" viewBox="0 0 12 14"><path d="M9 1L3 7l6 6" fill="none" stroke="#fff" stroke-width="2.5"/></svg></div>
  <div class="abs arrow-btn" style="right:34px"><svg width="12" height="14" viewBox="0 0 12 14"><path d="M3 1l6 6-6 6" fill="none" stroke="#fff" stroke-width="2.5"/></svg></div>
</section>
<svg class="abs hero-wave" viewBox="0 0 1200 124" preserveAspectRatio="none">
  <path d="M0 40 C300 110 700 120 1200 40 L1200 124 L0 124 Z" fill="#0293ce"/>
  <path d="M0 60 C320 130 720 130 1200 60 L1200 124 L0 124 Z" fill="#eef1f3"/>
</svg>

<!-- upload band -->
<section class="abs band">
  <p class="abs band-text">At vero eos et accusamus et iusto odio dignissimos ducimus qui blanditiis praesentium voluptatum deleniti</p>
  <span class="abs upload"><svg width="14" height="14" viewBox="0 0 24 24"><path d="M12 3l-6 6h4v7h4V9h4z M4 19h16v3H4z" fill="#ec1f27"/></svg>Upload an Practice Schedules</span>
</section>

<!-- registration -->
<h2 class="abs heading reg-title">Multi Step Registration Process</h2>
<p class="abs reg-intro">Nam libero tempore, cum soluta nobis est eligendi optio cumque nihil impedit quo minus id quod maxime placeat facere possimus, omnis voluptas assumenda repeat quibusdam et aut officiis debitis aut rerum necessitatibus saepe eveniet ut et voluptates repudiandae sint et molestiae.</p>

<div class="abs step" style="left:81px">
  <div class="step-circle"><svg width="56" height="42" viewBox="0 0 56 42"><rect x="2" y="2" width="52" height="38" rx="5" fill="none" stroke="#0293ce" stroke-width="4"/><rect x="2" y="11" width="52" height="7" fill="#0293ce"/><rect x="9" y="27" width="14" height="4" fill="#0293ce"/></svg></div>
  <div class="step-label">Pay Fees</div>
  <p class="step-text">Nam libero tempore, cum soluta no bis est eligendi optio cumque nihil impe dit quo minus quod max</p>
</div>
<div class="abs step" style="left:339px">
  <div class="step-circle"><svg width="56" height="50" viewBox="0 0 56 50"><path d="M4 2v44h50" fill="none" stroke="#0293ce" stroke-width="4"/><rect x="12" y="24" width="7" height="18" fill="#0293ce"/><rect x="23" y="14" width="7" height="28" fill="#0293ce"/><rect x="34" y="20" width="7" height="22" fill="#0293ce"/><rect x="45" y="8" width="7" height="34" fill="#0293ce"/></svg></div>
  <div class="step-label">Sign Waivers</div>
  <p class="step-text">Nam libero tempore, cum soluta no bis est eligendi optio cumque nihil impe dit quo minus quod max</p>
</div>
<div class="abs step" style="left:597px">
  <div class="step-circle"><svg width="54" height="54" viewBox="0 0 54 54"><circle cx="27" cy="27" r="25" fill="#0293ce"/><path d="M15 28l8 8 16-17" fill="none" stroke="#fff" stroke-width="6" stroke-linecap="round" stroke-linejoin="round"/></svg></div>
  <div class="step-label">Reserve a Spot</div>
  <p class="step-text">Nam libero tempore, cum soluta no bis est eligendi optio cumque nihil impe dit quo minus quod max</p>
</div>
<div class="abs step" style="left:857px">
  <div class="step-circle"><svg width="64" height="52" viewBox="0 0 64 52"><circle cx="32" cy="12" r="10" fill="#0293ce"/><circle cx="12" cy="18" r="7" fill="#0293ce"/><circle cx="52" cy="18" r="7" fill="#0293ce"/><path d="M16 50c0-16 7-24 16-24s16 8 16 24z" fill="#0293ce"/><path d="M0 46c0-12 5-18 12-18 3 0 5 1 7 3-3 4-5 9-5 15z M64 46c0-12-5-18-12-18-3 0-5 1-7 3 3 4 5 9 5 15z" fill="#0293ce"/></svg></div>
  <div class="step-label">Buy National Membership</div>
  <p class="step-text">Nam libero tempore, cum soluta no bis est eligendi optio cumque nihil impe dit quo minus quod max</p>
</div>
<svg class="abs step-arrow" style="left:300px" width="60" height="50" viewBox="0 0 60 50"><path d="M2 10 C25 8 40 20 52 36 M40 36h13V22" fill="none" stroke="#bbb" stroke-width="2"/></svg>
<svg class="abs step-arrow" style="left:558px" width="60" height="50" viewBox="0 0 60 50"><path d="M2 40 C25 40 40 28 52 12 M40 10h13v13" fill="none" stroke="#bbb" stroke-width="2"/></svg>
<svg class="abs step-arrow" style="left:818px" width="60" height="50" viewBox="0 0 60 50"><path d="M2 10 C25 8 40 20 52 36 M40 36h13V22" fill="none" stroke="#bbb" stroke-width="2"/></svg>

<div class="abs rule" style="top:1195px"></div>

<!-- special events -->
<h2 class="abs heading col-title" style="left:98px;top:1250px">Special Events</h2>

<article class="abs event" style="top:1320px">
  <div class="event-img" role="img" aria-label="Swimmers practising in the pool" style="background:linear-gradient(135deg,#2bb3b8,#6fd0cd 60%,#1f9ea6)"></div>
  <div class="event-body"><h3 class="event-title">Smilique sunt in culpa qui officia deserunt</h3>
  <div class="meta"><span><b>▦</b> Jul 29, 2016</span><span><b>●</b> John</span><span><b>✉</b> 0 Comments</span></div>
  <p class="event-text">At vero eos et accusamus et iusto odio dignissimos ducimus qui blanditiis praesentium voluptatum deleniti atque corrupti quos dolores et quas molestias excepturi.</p>
  <p class="more" style="margin-top:12px">Read More &gt;&gt;</p></div>
</article>
<article class="abs event" style="top:1546px">
  <div class="event-img" role="img" aria-label="Team in red suits posing in a line in the water" style="background:linear-gradient(135deg,#7fb0b6,#c8d3d2 50%,#b3585c)"></div>
  <div class="event-body"><h3 class="event-title">Smilique sunt in culpa qui officia deserunt</h3>
  <div class="meta"><span><b>▦</b> Jul 29, 2016</span><span><b>●</b> John</span><span><b>✉</b> 0 Comments</span></div>
  <p class="event-text">At vero eos et accusamus et iusto odio dignissimos ducimus qui blanditiis praesentium voluptatum deleniti atque corrupti quos dolores et quas molestias excepturi.</p>
  <p class="more" style="margin-top:12px">Read More &gt;&gt;</p></div>
</article>
<article class="abs event" style="top:1772px">
  <div class="event-img" role="img" aria-label="Swimmer floating on her back" style="background:linear-gradient(135deg,#3fd0e2,#7fe3ee 60%,#2cc0d6)"></div>
  <div class="event-body"><h3 class="event-title">Smilique sunt in culpa qui officia deserunt</h3>
  <div class="meta"><span><b>▦</b> Jul 29, 2016</span><span><b>●</b> John</span><span><b>✉</b> 0 Comments</span></div>
  <p class="event-text">At vero eos et accusamus et iusto odio dignissimos ducimus qui blanditiis praesentium voluptatum deleniti atque corrupti quos dolores et quas molestias excepturi.</p>
  <p class="more" style="margin-top:12px">Read More &gt;&gt;</p></div>
</article>
<article class="abs event" style="top:1998px">
  <div class="event-img" role="img" aria-label="Swimmer gliding through the water" style="background:linear-gradient(135deg,#4cc4c9,#9adfe0 55%,#38aeb6)"></div>
  <div class="event-body"><h3 class="event-title">Smilique sunt in culpa qui officia deserunt</h3>
  <div class="meta"><span><b>▦</b> Jul 29, 2016</span><span><b>●</b> John</span><span><b>✉</b> 0 Comments</span></div>
  <p class="event-text">At vero eos et accusamus et iusto odio dignissimos ducimus qui blanditiis praesentium voluptatum deleniti atque corrupti quos dolores et quas molestias excepturi.</p>
  <p class="more" style="margin-top:12px">Read More &gt;&gt;</p></div>
</article>
<article class="abs event" style="top:2224px;border-bottom:none">
  <div class="event-img" role="img" aria-label="Swimmer in a red cap doing a routine" style="background:linear-gradient(135deg,#2a9ea6,#62c3c4 55%,#258d97)"></div>
  <div class="event-body"><h3 class="event-title">Smilique sunt in culpa qui officia deserunt</h3>
  <div class="meta"><span><b>▦</b> Jul 29, 2016</span><span><b>●</b> John</span><span><b>✉</b> 0 Comments</span></div>
  <p class="event-text">At vero eos et accusamus et iusto odio dignissimos ducimus qui blanditiis praesentium voluptatum deleniti atque corrupti quos dolores et quas molestias excepturi.</p>
  <p class="more" style="margin-top:12px">Read More &gt;&gt;</p></div>
</article>
<p class="abs more" style="left:98px;top:2450px">View More &gt;&gt;</p>

<!-- calendar -->
<h2 class="abs heading col-title" style="left:764px;top:1250px">Team Calendar</h2>
<div class="abs calendar">
  <div class="cal-head"><span>◂</span><span>DEC 2016</span><span>▸</span></div>
  <div class="cal-grid">
    <span class="dow">Su</span><span class="dow">Mo</span><span class="dow">Tu</span><span class="dow">We</span><span class="dow">Th</span><span class="dow">Fr</span><span class="dow">Sa</span>
    <span class="d empty"></span><span class="d empty"></span><span class="d empty"></span><span class="d">1</span><span class="d today">2</span><span class="d">3</span><span class="d">4</span>
    <span class="d">5</span><span class="d">6</span><span class="d">7</span><span class="d">8</span><span class="d">9</span><span class="d">10</span><span class="d">11</span>
    <span class="d">12</span><span class="d">13</span><span class="d">14</span><span class="d">15</span><span class="d">16</span><span class="d">17</span><span class="d">18</span>
    <span class="d">19</span><span class="d">20</span><span class="d">21</span><span class="d">22</span><span class="d">23</span><span class="d">24</span><span class="d">25</span>
    <span class="d">26</span><span class="d">27</span><span class="d">28</span><span class="d">29</span><span class="d">30</span><span class="d">31</span><span class="d empty"></span>
  </div>
</div>

<!-- news -->
<h2 class="abs heading col-title" style="left:764px;top:1686px">News</h2>
<div class="abs news-item" style="top:1732px">
  <div class="news-img" role="img" aria-label="Team members on the pool deck" style="background:linear-gradient(135deg,#b85a5a,#d9a3a0 50%,#6aa7b0)"></div>
  <div class="news-body"><p class="news-title">Finibus Bonorum et Malorum</p><div class="meta"><span><b>▦</b> Jul 29, 2016</span><span><b>●</b> John</span></div></div>
</div>
<div class="abs news-item" style="top:1826px">
  <div class="news-img" role="img" aria-label="Swimmers in the pool" style="background:linear-gradient(135deg,#3aa6b0,#8bd0d2)"></div>
  <div class="news-body"><p class="news-title">Finibus Bonorum et Malorum</p><div class="meta"><span><b>▦</b> Jul 29, 2016</span><span><b>●</b> John</span></div></div>
</div>
<div class="abs news-item" style="top:1920px">
  <div class="news-img" role="img" aria-label="Young swimmer at the pool" style="background:linear-gradient(135deg,#c9a08d,#e7cbbd 55%,#8cc6cf)"></div>
  <div class="news-body"><p class="news-title">Finibus Bonorum et Malorum</p><div class="meta"><span><b>▦</b> Jul 29, 2016</span><span><b>●</b> John</span></div></div>
</div>
<div class="abs news-item" style="top:2014px;border-bottom:none">
  <div class="news-img" role="img" aria-label="Colourful performance costume" style="background:linear-gradient(135deg,#e8a23a,#f3cf6b 50%,#d6493f)"></div>
  <div class="news-body"><p class="news-title">Finibus Bonorum et Malorum</p><div class="meta"><span><b>▦</b> Jul 29, 2016</span><span><b>●</b> John</span></div></div>
</div>
<p class="abs more" style="left:764px;top:2140px">View More &gt;&gt;</p>

<!-- video -->
<h2 class="abs heading col-title" style="left:764px;top:2198px">Video</h2>
<div class="abs video" role="img" aria-label="Video still of a swimmer in a red suit performing"></div>
<div class="abs play"><svg width="18" height="20" viewBox="0 0 18 20"><path d="M2 1l15 9-15 9z" fill="#fff"/></svg></div>

<div class="abs rule" style="top:2503px"></div>

<!-- photos -->
<h2 class="abs heading col-title" style="left:98px;top:2546px">Photos</h2>
<div class="abs photos">
  <div role="img" aria-label="Swimmer's arm above water" style="background:linear-gradient(135deg,#5ca9ad,#b9a27d)"></div>
  <div role="img" aria-label="Legs raised above the water" style="background:linear-gradient(135deg,#e0b24a,#3aa3b4)"></div>
  <div role="img" aria-label="Team lined up at the pool edge" style="background:linear-gradient(135deg,#9ad0e0,#d98f8f)"></div>
  <div role="img" aria-label="Swimmers in the pool from above" style="background:linear-gradient(135deg,#2c8f97,#6fc0c0)"></div>
  <div role="img" aria-label="Swimmer mid-stroke" style="background:linear-gradient(135deg,#3fb0d6,#a5dbe8)"></div>
  <div role="img" aria-label="Swimmers in a bright pool" style="background:linear-gradient(135deg,#43c3e2,#d34a4a)"></div>
  <div role="img" aria-label="Team sketch artwork" style="background:linear-gradient(135deg,#e6e6e6,#bdbdbd)"></div>
  <div role="img" aria-label="Two young swimmers posing" style="background:linear-gradient(135deg,#c2a690,#d46b8a)"></div>
</div>

<!-- social feed -->
<h2 class="abs heading col-title" style="left:741px;top:2546px">Social Feed</h2>
<div class="abs feed">
  <div class="feed-cover" role="img" aria-label="Team page cover photo of the pool"></div>
  <div class="feed-badge"><span style="width:40px;height:40px;border-radius:50%;background:var(--aqua)"></span></div>
  <div class="feed-name">MARIGOLD CLUB</div>
  <div class="feed-likes">4,993 likes</div>
  <div class="feed-btn" style="left:14px">▣ Like Page</div>
  <div class="feed-btn" style="right:14px">✎ Sign Up</div>
  <p class="feed-note">Be the first of your friends to like this</p>
  <div class="feed-faces">
    <div style="background:#b89c8a"></div><div style="background:#8c9fb0"></div><div style="background:#c7a68f"></div><div style="background:#9e8b7c"></div><div style="background:#a9b7c2"></div><div style="background:#c09c94"></div><div style="background:#8fa6a0"></div>
  </div>
</div>

<!-- sponsors -->
<section class="abs sponsors"></section>
<h2 class="abs heading sp-title">Our Sponsors</h2>
<svg class="abs sp-arrow" style="left:86px" width="14" height="24" viewBox="0 0 14 24"><path d="M12 2L2 12l10 10" fill="none" stroke="#888" stroke-width="2.5"/></svg>
<svg class="abs sp-arrow" style="right:86px" width="14" height="24" viewBox="0 0 14 24"><path d="M2 2l10 10-10 10" fill="none" stroke="#888" stroke-width="2.5"/></svg>
<div class="abs sp-row">
  <div class="sp-logo">Quillfin</div>
  <div class="sp-logo">Envoya</div>
  <div class="sp-logo">Lumora</div>
  <div class="sp-logo">Tidewell</div>
  <div class="sp-logo">Kelpworks</div>
</div>
<svg class="abs foot-wave" viewBox="0 0 1200 90" preserveAspectRatio="none">
  <path d="M0 20 C300 90 800 70 1200 10 L1200 90 L0 90 Z" fill="#0f78b3"/>
  <path d="M0 40 C350 100 800 90 1200 30 L1200 90 L0 90 Z" fill="#1789c8"/>
</svg>

<!-- footer -->
<footer class="abs footer"></footer>
<div class="abs f-col" style="left:98px">
  <h4 class="f-head">Information</h4>
  <ul class="f-list"><li>About Us</li><li>Careers</li><li>Privacy &amp; Security</li><li>Site Map</li><li>Terms of Use</li><li>Blog</li></ul>
</div>
<div class="abs f-col" style="left:295px">
  <h4 class="f-head">Help &amp; support</h4>
  <ul class="f-list"><li>Rashguards</li><li>Boardshorts</li><li>Wetsuits</li><li>Kids Swimwear</li><li>Plus Size Swimwear</li><li>Swim Parkas</li></ul>
</div>
<div class="abs f-col" style="left:506px;width:230px">
  <h4 class="f-head">Contact Us</h4>
  <div class="f-contact"><svg width="14" height="18" viewBox="0 0 14 18"><path d="M7 0a7 7 0 00-7 7c0 5 7 11 7 11s7-6 7-11a7 7 0 00-7-7zm0 10a3 3 0 110-6 3 3 0 010 6z" fill="#fff"/></svg><span>At vero eos et accusamus et ius dignissimos ducimus qui</span></div>
  <div class="f-contact"><svg width="16" height="16" viewBox="0 0 24 24"><path fill="#fff" d="M6.6 10.8a15 15 0 006.6 6.6l2.2-2.2c.3-.3.7-.4 1-.2 1.1.4 2.3.6 3.6.6.6 0 1 .4 1 1V20c0 .6-.4 1-1 1A17 17 0 013 4c0-.6.4-1 1-1h3.5c.6 0 1 .4 1 1 0 1.3.2 2.5.6 3.6.1.3 0 .7-.2 1z"/></svg><span>1-555-010-0199</span></div>
  <div class="f-contact"><svg width="16" height="12" viewBox="0 0 24 18"><rect x="1" y="1" width="22" height="16" rx="2" fill="#fff"/><path d="M1 2l11 8 11-8" fill="none" stroke="#1789c8" stroke-width="2"/></svg><span>hello@marigoldclub.org</span></div>
</div>
<div class="abs f-col" style="left:776px;width:330px">
  <h4 class="f-head">Email Subscription</h4>
  <p style="font-size:12.5px">Register your email address to get information about us</p>
  <div class="f-input"><span class="field">Email Address</span><span class="go">Subscribe</span></div>
  <h4 class="f-head" style="margin-top:18px;margin-bottom:0">Stay Connected</h4>
  <div class="socials">
    <span style="background:#6bb35a"></span><span style="background:#3a5ea8"></span><span style="background:#39a9e0"></span><span style="background:#d9493a"></span><span style="background:#2f6fa8"></span><span style="background:#7a57a8"></span><span style="background:#d12c2c"></span><span style="background:#c8232c"></span>
  </div>
</div>
<p class="abs copy">Copyright © 2016 Marigold Club. All Rights Reserved &nbsp;|&nbsp; Privacy Policy &nbsp;|&nbsp; Terms of Use &nbsp;|&nbsp; Feedback</p>

</body>
</html>
```